Redesign of business card for Cedar Ridge Mechanical

We are looking for a new design for our business cards for Cedar Ridge Mechanical. We are a plumbing & HVAC construction company, operating on the West Coast of Canada and USA. Logo attached.
Industry/Entity Type
Construction - Plumbing & HVAC
Contact Information for Business Card
Name, address, phone numbers, email, website address
Look and feel
Each slider illustrates characteristics of the customer's brand and the style your logo design should communicate.

```html
<!DOCTYPE html>
<html lang="en">
<head>
<meta charset="utf-8">
<title>Cedar Ridge Mechanical – Business Card</title>
<link href="https://fonts.googleapis.com/css2?family=Poppins:wght@300;400;600&display=swap" rel="stylesheet">
<style>
  :root {
    --backdrop: #222223;
    --card: #1c1c1e;
    --card-edge: #0e0e0f;
    --ink: #ffffff;
    --ink-soft: #d9d9d9;
    --divider: #8a8a8a;
    --pattern-a: #1a1a1c;
    --pattern-b: #2b2b2e;
  }
  * { box-sizing: border-box; margin: 0; padding: 0; }
  html, body {
    width: 1200px; height: 780px; overflow: hidden;
    background: var(--backdrop);
    font-family: "Poppins", sans-serif;
    color: var(--ink);
  }
  .stage {
    position: relative; width: 1200px; height: 780px;
    display: flex; align-items: center; justify-content: center; gap: 40px;
  }
  .card {
    position: relative; width: 540px; height: 310px;
    background: var(--card);
    box-shadow: 0 3px 0 var(--card-edge), 0 6px 0 var(--card-edge), 0 22px 40px rgba(0,0,0,.55);
    overflow: hidden;
  }
  /* front */
  .brand {
    position: absolute; left: 36px; top: 44px;
    display: flex; align-items: center; gap: 12px;
  }
  .brand-square { width: 22px; height: 22px; background: var(--ink); }
  .brand-name {
    font-weight: 600; font-size: 19px; line-height: 1.2; letter-spacing: .02em;
    text-transform: uppercase; width: 180px;
  }
  .address {
    position: absolute; left: 36px; bottom: 34px; width: 230px;
    font-size: 12px; font-weight: 300; line-height: 1.6; color: var(--ink-soft);
  }
  .divider {
    position: absolute; left: 0; top: 0; width: 540px; height: 310px;
  }
  .person { position: absolute; left: 300px; top: 66px; }
  .person-name { font-size: 25px; line-height: 1.1; font-weight: 300; white-space: nowrap; }
  .person-name strong { font-weight: 600; }
  .person-title { font-size: 13px; font-weight: 400; margin-top: 4px; }
  .contacts { list-style: none; margin-top: 26px; }
  .contacts li {
    display: flex; align-items: center; gap: 10px;
    font-size: 13px; font-weight: 300; line-height: 1; margin-bottom: 10px;
  }
  .contacts svg { width: 13px; height: 13px; flex: none; }
  /* back */
  .pattern-fill {
    position: absolute; inset: 0;
    background: linear-gradient(135deg, var(--pattern-a) 0%, var(--pattern-b) 60%, var(--pattern-a) 100%);
  }
</style>
</head>
<body>
<main class="stage">
  <section class="card card-front">
    <div class="brand">
      <span class="brand-square"></span>
      <span class="brand-name">Cedar Ridge Mechanical</span>
    </div>
    <p class="address">1840 Harbor Ln. Suite 310<br>Bellingham, WA 98225</p>
    <svg class="divider" viewBox="0 0 540 310" aria-hidden="true">
      <line x1="290" y1="48" x2="250" y2="262" stroke="var(--divider)" stroke-width="1"/>
    </svg>
    <div class="person">
      <h1 class="person-name"><strong>Marta</strong> Kovalen</h1>
      <p class="person-title">Founder &amp; CEO</p>
      <ul class="contacts">
        <li>
          <svg viewBox="0 0 24 24" fill="var(--ink)" aria-hidden="true"><path d="M6.6 10.8a15.2 15.2 0 0 0 6.6 6.6l2.2-2.2a1 1 0 0 1 1-.25 11.4 11.4 0 0 0 3.6.57 1 1 0 0 1 1 1V20a1 1 0 0 1-1 1A17 17 0 0 1 3 4a1 1 0 0 1 1-1h3.5a1 1 0 0 1 1 1c0 1.25.2 2.45.57 3.57a1 1 0 0 1-.25 1z"/></svg>
          (555) 014-2290
        </li>
        <li>
          <svg viewBox="0 0 24 24" fill="none" stroke="var(--ink)" stroke-width="2" aria-hidden="true"><rect x="3" y="5" width="18" height="14" rx="1"/><path d="M3 6l9 7 9-7"/></svg>
          info@cedarridgemech.com
        </li>
        <li>
          <svg viewBox="0 0 24 24" fill="none" stroke="var(--ink)" stroke-width="2" aria-hidden="true"><circle cx="12" cy="12" r="9"/><path d="M3 12h18M12 3c3 3.5 3 14.5 0 18M12 3c-3 3.5-3 14.5 0 18"/></svg>
          www.cedarridgemech.com
        </li>
      </ul>
    </div>
  </section>

  <section class="card card-back">
    <div class="pattern-fill" role="img" aria-label="Repeating tonal pattern of the company mark across a black card back"></div>
  </section>
</main>
</body>
</html>
```